Mindfulness School for Children -- Business Cards

We're looking for business cards for our school directors and owners. We're a mindfulness school for children called little lanterns. Attached are our logos/icons.

```html
<!DOCTYPE html>
<html lang="en">
<head>
<meta charset="utf-8">
<title>little lanterns — business cards</title>
<link rel="stylesheet" href="https://fonts.googleapis.com/css2?family=Source+Sans+3:wght@400;600;700&display=swap">
<style>
  :root {
    --backdrop: #2b2f38;
    --teal-light: #5aaabd;
    --teal-mid: #3f91a4;
    --teal-dark: #2a6f80;
    --paper: #eef0f4;
    --paper-shade: #dfe3ea;
    --ink: #1f2328;
    --name-green: #6aac8e;
    --name-blue: #3a8db0;
    --brand: #4a97ad;
    --decor: #c9d2dc;
    --tab: #b9bcc2;
    --white: #ffffff;
  }
  * { box-sizing: border-box; margin: 0; padding: 0; }
  html, body { width: 1200px; height: 1000px; overflow: hidden; }
  body {
    background: var(--backdrop);
    font-family: "Source Sans 3", sans-serif;
    position: relative;
  }
  .card {
    position: absolute;
    left: 290px;
    width: 620px;
    height: 380px;
    border-radius: 24px;
    overflow: hidden;
    box-shadow: 0 14px 30px rgba(0,0,0,0.35);
  }
  .card-front { top: 90px; background: var(--teal-mid); }
  .card-back { top: 530px; background: linear-gradient(180deg, var(--paper), var(--paper-shade)); }

  .front-pattern {
    position: absolute; inset: 0;
    background:
      linear-gradient(30deg, rgba(0,45,60,0.32) 0%, rgba(0,45,60,0.08) 40%, rgba(255,255,255,0.06) 60%, rgba(255,255,255,0.22) 100%),
      linear-gradient(160deg, var(--teal-light), var(--teal-dark));
  }
  .front-brand {
    position: absolute; left: 170px; top: 258px;
    display: flex; align-items: center; gap: 10px;
  }
  .front-brand-dot { width: 16px; height: 16px; border-radius: 50%; background: var(--white); }
  .front-brand-name { color: var(--white); font-weight: 600; font-size: 24px; line-height: 1; }

  .back-decor {
    position: absolute; right: 40px; top: -40px;
    width: 300px; height: 300px; border-radius: 50%;
    background: radial-gradient(circle, rgba(201,210,220,0.9) 0%, rgba(201,210,220,0.35) 55%, rgba(201,210,220,0) 72%);
  }
  .edge-tab {
    position: absolute; left: 0; top: 176px; width: 10px; height: 28px; background: var(--tab);
  }
  .person { position: absolute; left: 56px; top: 58px; }
  .person-name { font-size: 24px; font-weight: 700; line-height: 1.1; }
  .person-name .first { color: var(--name-green); }
  .person-name .last { color: var(--name-blue); }
  .person-title { font-size: 15px; color: var(--ink); margin-top: 2px; }

  .contact { position: absolute; left: 56px; bottom: 44px; font-size: 14px; color: var(--ink); line-height: 1.35; }
  .address { margin-bottom: 6px; }
  .contact-row { display: flex; align-items: center; gap: 8px; }
  .contact-row svg { width: 12px; height: 12px; fill: none; stroke: var(--name-blue); stroke-width: 1.6; }

  .brand-mark {
    position: absolute; right: 56px; top: 204px;
    display: flex; align-items: center; gap: 10px;
  }
  .brand-dot { width: 14px; height: 14px; border-radius: 50%; background: var(--brand); }
  .brand-name { font-size: 34px; font-weight: 400; color: var(--brand); line-height: 1; }
</style>
</head>
<body>

<section class="card card-front">
  <div class="front-pattern" role="img" aria-label="Repeating pattern of embossed lotus flowers in light and dark teal"></div>
  <div class="front-brand">
    <span class="front-brand-dot"></span>
    <span class="front-brand-name">little lanterns</span>
  </div>
</section>

<section class="card card-back">
  <div class="back-decor" role="img" aria-label="Large faint lotus flower decoration"></div>
  <div class="edge-tab"></div>

  <div class="person">
    <div class="person-name"><span class="first">Clara</span> <span class="last">Benning</span></div>
    <div class="person-title">Managing Director</div>
  </div>

  <div class="contact">
    <div class="address">2417 Maple Row Fairview<br>OR 97024, United States</div>
    <div class="contact-row">
      <svg viewBox="0 0 12 12"><path d="M2 1.5 L4.5 1.5 L5.2 4 L3.8 5 Q5 7.5 7 8.2 L8 6.8 L10.5 7.5 L10.5 10 Q5 10.5 1.5 4 Z"/></svg>
      <span>(+1) 555.014.2280</span>
    </div>
    <div class="contact-row">
      <svg viewBox="0 0 12 12"><rect x="1" y="2.5" width="10" height="7"/><path d="M1 2.5 L6 6.5 L11 2.5"/></svg>
      <span>info@littlelanterns.org</span>
    </div>
    <div class="contact-row">
      <svg viewBox="0 0 12 12"><circle cx="6" cy="6" r="4.8"/><ellipse cx="6" cy="6" rx="2" ry="4.8"/><path d="M1.2 6 H10.8"/></svg>
      <span>www.littlelanterns.org</span>
    </div>
  </div>

  <div class="brand-mark">
    <span class="brand-dot"></span>
    <span class="brand-name">little lanterns</span>
  </div>
</section>

</body>
</html>
```